Building Maintenance Company Capability Statement

We would like a capability statement designed please.

Let us know where we can supply the written text.

Ideally, most of the information will be on our website.
www.tallowbridgeco.com.au

Low design quality

Target Market(s)

Strata and building managers. schools and educational facilities, retirement and aged care.

Industry/Entity Type

Building

Font styles to use
Other font styles liked:
• nanito sans light

Requirements
Must have
• Images of people working (we can supply)
Easy to skim read
Colourful and attractive
Should not have
• lots of words

```html
<!DOCTYPE html>
<html lang="en">
<head>
<meta charset="utf-8">
<title>Tallowbridge Co – Capability Flyer</title>
<link href="https://fonts.googleapis.com/css2?family=Oswald:wght@400;500;600&family=Montserrat:wght@400;500;600&display=swap" rel="stylesheet">
<style>
  :root{
    --backdrop:#8fb0cc;
    --paper:#ffffff;
    --navy:#2d5f88;
    --mid-blue:#3d7fb8;
    --sky:#4fa6dc;
    --panel:#3f6d93;
    --red:#d8354a;
    --grey:#8a8a8a;
    --ink-grey:#6b6b6b;
    --tick:#bfe0f5;
  }
  *{box-sizing:border-box;margin:0;padding:0}
  html,body{width:1200px;height:800px;overflow:hidden;background:var(--backdrop)}
  .canvas{position:relative;width:1200px;height:800px}
  .flyer{position:absolute;left:330px;top:18px;width:540px;height:764px;background:var(--paper);overflow:hidden;box-shadow:0 10px 30px rgba(30,60,90,.25)}
  .flyer-art{position:absolute;inset:0}
  .tag{position:absolute;height:32px;border-radius:6px;color:#fff;font:500 17px/32px "Oswald",sans-serif;letter-spacing:2px;text-align:center}
  .tag--trusted{left:140px;top:432px;width:128px;background:var(--red)}
  .tag--reliable{left:278px;top:462px;width:128px;background:var(--mid-blue)}
  .tag--experienced{left:412px;top:492px;width:124px;background:var(--grey)}
  .headline{position:absolute;left:38px;top:478px;width:200px;font:500 26px/1.12 "Oswald",sans-serif;color:var(--ink-grey)}
  .headline .accent-red{color:var(--red)}
  .headline .accent-blue{color:var(--sky)}
  .headline-rule{position:absolute;left:38px;top:640px;width:26px;height:4px;background:var(--red)}
  .services{position:absolute;left:250px;top:530px;width:272px}
  .services-title{font:500 14px/18px "Oswald",sans-serif;color:var(--mid-blue);letter-spacing:2px;text-align:right;padding-right:18px;border-bottom:4px solid var(--navy);padding-bottom:3px;border-radius:0 0 4px 4px}
  .services-panel{margin-top:6px;background:var(--panel);border-radius:14px;padding:12px 12px 6px;display:grid;grid-template-columns:1fr 1fr;gap:0 10px}
  .services-panel ul{list-style:none}
  .services-panel li{display:flex;gap:6px;align-items:flex-start;font:400 10px/13px "Montserrat",sans-serif;color:#fff;margin-bottom:7px}
  .services-panel svg{flex:0 0 auto;margin-top:1px}
  .brand{position:absolute;left:38px;top:694px;font:600 15px/18px "Oswald",sans-serif;color:var(--navy);display:flex;align-items:center;gap:7px}
  .brand-dot{width:14px;height:14px;border-radius:50%;background:var(--red)}
  .contact-line{position:absolute;left:38px;font:400 10px/12px "Montserrat",sans-serif;color:var(--navy)}
  .contact-line--mail{top:718px}
  .contact-line--web{top:732px}
  .call{position:absolute;right:22px;top:698px;text-align:right}
  .call-label{font:400 14px/18px "Montserrat",sans-serif;color:var(--navy);letter-spacing:1px}
  .call-number{font:600 24px/28px "Montserrat",sans-serif;color:var(--red)}
</style>
</head>
<body>
<div class="canvas">
  <article class="flyer">
    <svg class="flyer-art" width="540" height="764" viewBox="0 0 540 764">
      <defs>
        <linearGradient id="fenceTone" x1="0" y1="0" x2="1" y2="1">
          <stop offset="0" stop-color="#d9d6cf"/><stop offset=".5" stop-color="#a89c88"/><stop offset="1" stop-color="#7d776d"/>
        </linearGradient>
        <linearGradient id="ropeTone" x1="0" y1="0" x2="0" y2="1">
          <stop offset="0" stop-color="#5f7390"/><stop offset=".55" stop-color="#c9c6bf"/><stop offset="1" stop-color="#e8e4da"/>
        </linearGradient>
      </defs>
      <path d="M0,250 C20,140 40,60 70,0 H0 Z" fill="#ffffff"/>
      <path d="M0,330 C40,200 60,90 90,0 H70 C40,80 15,180 0,260 Z" fill="var(--navy)"/>
      <path d="M0,400 C120,470 330,470 540,420 V440 C330,490 110,490 0,420 Z" fill="var(--sky)"/>
      <path d="M0,370 C120,450 330,455 540,400 V422 C330,472 110,470 0,395 Z" fill="var(--navy)"/>
      <path d="M0,330 C40,380 100,420 180,440 C90,400 40,360 0,340 Z" fill="var(--mid-blue)"/>
      <path role="img" aria-label="Photo: worker spray painting a timber fence" d="M100,0 H540 V395 C420,440 250,430 170,340 C110,270 85,120 100,0 Z" fill="url(#fenceTone)" stroke="#ffffff" stroke-width="3"/>
      <circle role="img" aria-label="Photo: rope access technician pressure cleaning a building wall" cx="430" cy="180" r="125" fill="url(#ropeTone)" stroke="#ffffff" stroke-width="5"/>
      <rect x="0" y="752" width="540" height="12" fill="var(--navy)"/>
      <rect x="0" y="748" width="540" height="4" fill="var(--sky)"/>
    </svg>

    <div class="tag tag--trusted">TRUSTED</div>
    <div class="tag tag--reliable">RELIABLE</div>
    <div class="tag tag--experienced">EXPERIENCED</div>

    <h1 class="headline">We Provide<br><span class="accent-red">Cost Effective<br>Solutions</span> To Your<br><span class="accent-blue">Building And<br>Maintainance</span></h1>
    <div class="headline-rule"></div>

    <section class="services">
      <h2 class="services-title">OUR SERVICES</h2>
      <div class="services-panel">
        <ul>
          <li><svg width="10" height="10" viewBox="0 0 10 10"><circle cx="5" cy="5" r="4.2" fill="none" stroke="var(--tick)"/><path d="M3 5.2 4.4 6.5 7 3.8" fill="none" stroke="var(--tick)"/></svg>Internal and External Painting Works</li>
          <li><svg width="10" height="10" viewBox="0 0 10 10"><circle cx="5" cy="5" r="4.2" fill="none" stroke="var(--tick)"/><path d="M3 5.2 4.4 6.5 7 3.8" fill="none" stroke="var(--tick)"/></svg>Electrical</li>
          <li><svg width="10" height="10" viewBox="0 0 10 10"><circle cx="5" cy="5" r="4.2" fill="none" stroke="var(--tick)"/><path d="M3 5.2 4.4 6.5 7 3.8" fill="none" stroke="var(--tick)"/></svg>Plumbing</li>
          <li><svg width="10" height="10" viewBox="0 0 10 10"><circle cx="5" cy="5" r="4.2" fill="none" stroke="var(--tick)"/><path d="M3 5.2 4.4 6.5 7 3.8" fill="none" stroke="var(--tick)"/></svg>Roofing</li>
        </ul>
        <ul>
          <li><svg width="10" height="10" viewBox="0 0 10 10"><circle cx="5" cy="5" r="4.2" fill="none" stroke="var(--tick)"/><path d="M3 5.2 4.4 6.5 7 3.8" fill="none" stroke="var(--tick)"/></svg>Plastering</li>
          <li><svg width="10" height="10" viewBox="0 0 10 10"><circle cx="5" cy="5" r="4.2" fill="none" stroke="var(--tick)"/><path d="M3 5.2 4.4 6.5 7 3.8" fill="none" stroke="var(--tick)"/></svg>Carpentry and Repairs</li>
          <li><svg width="10" height="10" viewBox="0 0 10 10"><circle cx="5" cy="5" r="4.2" fill="none" stroke="var(--tick)"/><path d="M3 5.2 4.4 6.5 7 3.8" fill="none" stroke="var(--tick)"/></svg>AC Installations</li>
          <li><svg width="10" height="10" viewBox="0 0 10 10"><circle cx="5" cy="5" r="4.2" fill="none" stroke="var(--tick)"/><path d="M3 5.2 4.4 6.5 7 3.8" fill="none" stroke="var(--tick)"/></svg>Landscaping</li>
        </ul>
      </div>
    </section>

    <div class="brand"><span class="brand-dot"></span>TALLOWBRIDGE CO</div>
    <p class="contact-line contact-line--mail">hello@tallowbridgeco.com.au</p>
    <p class="contact-line contact-line--web">www.tallowbridgeco.com.au</p>

    <div class="call">
      <p class="call-label">CONTACT US</p>
      <p class="call-number">(08) 5550 1234</p>
    </div>
  </article>
</div>
</body>
</html>
```